Business Cards for a law firm

Business cards for our law firm. Use our silhoette logo and OAK PARTNERS - check our website (www.oakpartners.example)

Contact Information for Business Card

our silhouette logo, OAK PARTNERS, 800-555-0147, Dorian Pemberton, dorian@oakpartners.example

Requirements
Must have
• our silhouette logo, OAK PARTNERS, 800-555-0147, Dorian Pemberton, dorian@oakpartners.example

```html
<!DOCTYPE html>
<html lang="en">
<head>
<meta charset="utf-8">
<title>Oak Partners – Business Cards</title>
<link rel="stylesheet" href="https://fonts.googleapis.com/css2?family=Hind:wght@600;700&family=Montserrat:wght@400;600&display=swap">
<style>
  :root {
    --navy: #22316b;
    --ink: #1e1e24;
    --paper: #ffffff;
    --backdrop: #e9e9eb;
  }
  * { margin: 0; padding: 0; box-sizing: border-box; }
  html, body { width: 1200px; height: 1108px; overflow: hidden; }
  body { background: var(--backdrop); position: relative; font-family: "Montserrat", sans-serif; }

  .card { position: absolute; background: var(--paper); }
  .card--front { left: 219px; top: 50px; width: 774px; height: 473px; }
  .card--back  { left: 217px; top: 568px; width: 776px; height: 456px; }

  .brand { position: absolute; display: flex; align-items: center; color: var(--navy); }
  .brand__mark { background: var(--navy); flex: none; }
  .brand__name { font-family: "Montserrat", sans-serif; font-weight: 600; white-space: nowrap; }

  .card--front .brand { left: 100px; top: 242px; transform: translateY(-50%); gap: 12px; }
  .card--front .brand__mark { width: 30px; height: 30px; }
  .card--front .brand__name { font-size: 21px; letter-spacing: 2px; }

  .divider { position: absolute; left: 381px; top: 182px; width: 2px; height: 156px; background: var(--navy); }

  .contact { position: absolute; left: 394px; top: 182px; }
  .contact__name { font-family: "Hind", sans-serif; font-weight: 700; font-size: 31px; line-height: 36px; color: var(--navy); }
  .contact__role { font-size: 17px; color: var(--ink); margin-top: 0; line-height: 24px; }
  .contact__list { list-style: none; margin-top: 10px; }
  .contact__item { display: flex; align-items: center; gap: 9px; font-size: 17.5px; line-height: 30.5px; color: var(--ink); }
  .contact__icon { width: 17px; height: 17px; flex: none; fill: var(--navy); }

  .card--back .brand { left: 80px; top: 243px; transform: translateY(-50%); gap: 22px; }
  .card--back .brand__mark { width: 84px; height: 84px; }
  .card--back .brand__name { font-size: 44px; letter-spacing: 4px; }
</style>
</head>
<body>
  <section class="card card--front" aria-label="Front of business card">
    <div class="brand">
      <span class="brand__mark" aria-hidden="true"></span>
      <span class="brand__name">OAK PARTNERS</span>
    </div>
    <span class="divider" aria-hidden="true"></span>
    <div class="contact">
      <h1 class="contact__name">Dorian Pemberton</h1>
      <p class="contact__role">Lawyer</p>
      <ul class="contact__list">
        <li class="contact__item">
          <svg class="contact__icon" viewBox="0 0 24 24" aria-hidden="true"><path d="M6.6 10.8a15.1 15.1 0 0 0 6.6 6.6l2.2-2.2a1 1 0 0 1 1-.25 11.4 11.4 0 0 0 3.6.57 1 1 0 0 1 1 1V20a1 1 0 0 1-1 1A17 17 0 0 1 3 4a1 1 0 0 1 1-1h3.5a1 1 0 0 1 1 1c0 1.25.2 2.45.57 3.57a1 1 0 0 1-.25 1z"/></svg>
          <span>800-555-0147</span>
        </li>
        <li class="contact__item">
          <svg class="contact__icon" viewBox="0 0 24 24" aria-hidden="true"><path d="M3 6h18v12H3z" fill="none"/><path d="M3 7l9 6 9-6v11H3z"/><path d="M3 5.5h18L12 11.5z"/></svg>
          <span>dorian@oakpartners.example</span>
        </li>
        <li class="contact__item">
          <svg class="contact__icon" viewBox="0 0 24 24" aria-hidden="true"><circle cx="12" cy="12" r="9.5" fill="none" stroke="#22316b" stroke-width="2"/><path d="M12 2.5c-3 3-3 16 0 19M12 2.5c3 3 3 16 0 19M3 12h18" fill="none" stroke="#22316b" stroke-width="1.6"/></svg>
          <span>www.oakpartners.example</span>
        </li>
      </ul>
    </div>
  </section>

  <section class="card card--back" aria-label="Back of business card">
    <div class="brand">
      <span class="brand__mark" aria-hidden="true"></span>
      <span class="brand__name">OAK PARTNERS</span>
    </div>
  </section>
</body>
</html>
```